Profesional personal website needs design and business card

I need a business card with my professional name as a logo "Dorian Vitality" for my business. I am a Wellness Coach, consultant and trainer. So it should be professional, wellness oriented and modern.

Target Market(s)

Private clients, governments, corporations. Luxury and high market.

Industry/Entity Type

Health And Wellness

Contact Information for Business Card

Dorian Vitality should be the logo

Colors

Designer to choose colors to be used in the design.

Requirements
Must have
• Dorian Vitality
• Name: Tomás Lirandel
• Wellness Coach, Consultant & Trainer.
• Website: www.dorianvitality-example.com
• Phone:
• Spain (+34) 612 480 317
• (USA) +1 (555) 610 4829
Nice to have
• The most important is the design of "Dorian Vitality", as this is going to be my personal brand logo. It should be professional, wellness, high end and actual.
Should not have
• no golds, no baroque style..

```html
<!DOCTYPE html>
<html lang="en">
<head>
<meta charset="utf-8">
<title>Dorian Vitality — Business Card</title>
<link href="https://fonts.googleapis.com/css2?family=Montserrat:wght@400;500;700;800&display=swap" rel="stylesheet">
<style>
  :root {
    --bg: #1e1e1e;
    --card: #2a2a2a;
    --card-edge: #242424;
    --accent: #f7c300;
    --brand-blue: #1a1fb3;
    --front-mark: #8a8a8a;
    --text: #f2f2f2;
  }
  * { box-sizing: border-box; margin: 0; padding: 0; }
  html, body { width: 1200px; height: 900px; overflow: hidden; background: var(--bg); }
  body { font-family: "Montserrat", sans-serif; color: var(--text); position: relative; }

  .card {
    position: absolute;
    left: 250px;
    width: 700px;
    height: 400px;
    background: linear-gradient(135deg, var(--card) 0%, var(--card-edge) 100%);
    border-bottom: 7px solid var(--accent);
    box-shadow: 0 14px 30px rgba(0,0,0,.5);
  }
  .card--front { top: 35px; }
  .card--back { top: 465px; }

  /* front */
  .front-mark {
    position: absolute; inset: 0;
    display: flex; flex-direction: column; align-items: center; justify-content: center;
    color: var(--front-mark); font-weight: 700;
  }
  .front-mark .mark-main { font-size: 74px; letter-spacing: 1px; line-height: 1; }
  .front-mark .mark-sub { font-size: 30px; letter-spacing: 16px; margin-top: 4px; padding-left: 16px; }

  /* back */
  .brand {
    position: absolute; left: 60px; top: 150px; width: 260px;
    color: var(--brand-blue); font-weight: 800;
  }
  .brand .mark-main { font-size: 58px; line-height: 1; letter-spacing: 0; }
  .brand .mark-sub { font-size: 24px; letter-spacing: 10.5px; margin-top: 4px; }

  .divider {
    position: absolute; left: 345px; top: 110px; width: 2px; height: 190px;
    background: var(--accent);
  }

  .details { position: absolute; left: 375px; top: 112px; width: 310px; }
  .details .name { color: var(--accent); font-weight: 700; font-size: 25px; letter-spacing: 1px; }
  .details .role { font-size: 15px; line-height: 1.35; margin-top: 4px; font-weight: 500; }
  .contact { list-style: none; margin-top: 12px; font-size: 15px; }
  .contact li { display: flex; align-items: center; gap: 10px; height: 26px; white-space: nowrap; }
  .contact svg { width: 14px; height: 14px; flex: none; }
  .contact .site-name { color: var(--accent); }
  .flag { width: 24px; height: 15px; margin-left: auto; flex: none; }
</style>
</head>
<body>
  <section class="card card--front">
    <div class="front-mark">
      <span class="mark-main">DORIAN</span>
      <span class="mark-sub">VITALITY</span>
    </div>
  </section>

  <section class="card card--back">
    <div class="brand">
      <div class="mark-main">DORIAN</div>
      <div class="mark-sub">VITALITY</div>
    </div>
    <div class="divider"></div>
    <div class="details">
      <h1 class="name">TOMÁS LIRANDEL</h1>
      <p class="role">Wellness Coach,<br>Consultant &amp; Trainer</p>
      <ul class="contact">
        <li>
          <svg viewBox="0 0 24 24"><path d="M6 2h4l2 5-3 2a11 11 0 0 0 6 6l2-3 5 2v4a2 2 0 0 1-2 2A18 18 0 0 1 4 4a2 2 0 0 1 2-2z" fill="var(--accent)"/></svg>
          <span>(+34) 612 480 317</span>
          <svg class="flag" viewBox="0 0 24 15" role="img" aria-label="Spain"><rect width="24" height="15" fill="#c60b1e"/><rect y="4" width="24" height="7" fill="#ffc400"/></svg>
        </li>
        <li>
          <svg viewBox="0 0 24 24"><rect x="6" y="2" width="12" height="20" rx="2" fill="none" stroke="var(--accent)" stroke-width="2"/><circle cx="12" cy="18" r="1.2" fill="var(--accent)"/></svg>
          <span>+1 (555) 610 4829</span>
          <svg class="flag" viewBox="0 0 24 15" role="img" aria-label="United States"><rect width="24" height="15" fill="#fff"/><g fill="#b22234"><rect width="24" height="1.6"/><rect y="3.2" width="24" height="1.6"/><rect y="6.4" width="24" height="1.6"/><rect y="9.6" width="24" height="1.6"/><rect y="12.8" width="24" height="1.6"/></g><rect width="10" height="8" fill="#3c3b6e"/></svg>
        </li>
        <li>
          <svg viewBox="0 0 24 24"><rect x="2" y="5" width="20" height="14" rx="1" fill="none" stroke="var(--accent)" stroke-width="2"/><path d="M2 6l10 7 10-7" fill="none" stroke="var(--accent)" stroke-width="2"/></svg>
          <span>info@dorianvitality-example.com</span>
        </li>
        <li>
          <svg viewBox="0 0 24 24"><circle cx="12" cy="12" r="10" fill="none" stroke="var(--accent)" stroke-width="2"/><path d="M2 12h20M12 2c3 3 3 17 0 20M12 2c-3 3-3 17 0 20" fill="none" stroke="var(--accent)" stroke-width="1.5"/></svg>
          <span>www.<span class="site-name">dorianvitality-example</span>.com</span>
        </li>
      </ul>
    </div>
  </section>
</body>
</html>
```